Revamp our wedding venue website

Currently we are using wordpress for our website and hoped to find a designer that can assist us with making the website prettier and more pleasing and draw more interest. www.velmorhall.com is our current site. We are connected to google business mail, so I would prefer to stay with this for now and update our gallery with new photos, blog page and putting the contact us form back on all the pages.

Target Market(s)

20-40 years of age, all ranges of styles and generally clients looking for a different modern feel vs. a hotel hall.

Industry/Entity Type

Wedding

Logo Text

1927 Velmor Hall

Number of Pages Required

4 page

Font styles to use
Serif

Requirements
Must have
• Light, airy feel. Romantic and informative. Mobile friendly and easy to contact us-preferred contact form on all pages. Gallery of photos. Previous reviews
Nice to have
• Bio of staff, maybe some videos, and fun things to do in the area for out of town guests. Maps and also venue blank floor plan.

```html
<!DOCTYPE html>
<html lang="en">
<head>
<meta charset="utf-8">
<title>1927 Velmor Hall — Weddings &amp; Events</title>
<link rel="stylesheet" href="https://fonts.googleapis.com/css2?family=Montserrat:wght@300;400;500;600;700&family=Raleway:wght@300;400;500&display=swap">
<style>
:root{
  --pink:#d6309b;
  --ink:#333333;
  --muted:#8a8a8a;
  --soft:#f4f4f4;
  --tab:#ebebeb;
  --white:#ffffff;
  --star:#f5b21a;
}
*{box-sizing:border-box;margin:0;padding:0}
html,body{width:1200px;height:2848px;overflow:hidden}
body{position:relative;background:var(--white);font-family:"Raleway",sans-serif;color:var(--ink)}
.abs{position:absolute}
.center{left:0;width:1200px;text-align:center}

/* header */
.topbar{top:0;left:0;width:1200px;height:95px;background:var(--white)}
.contact-mini{top:44px;font-family:"Montserrat",sans-serif;font-size:12px;color:var(--ink);display:flex;align-items:center;gap:8px}
.contact-mini svg{width:18px;height:18px}
.logo-tab{left:470px;top:20px;width:255px;height:75px;background:var(--tab);border-radius:14px 14px 0 0}
.brand{font-family:"Montserrat",sans-serif;font-weight:300;color:var(--pink);text-align:center;line-height:1.1}
.logo-tab .brand{margin-top:10px;font-size:22px}

.grey-band{top:95px;left:0;width:1200px;height:425px;background:var(--soft)}
.nav{top:130px;display:flex;justify-content:center;gap:38px;font-family:"Montserrat",sans-serif;font-size:11px;font-weight:500;color:var(--ink);letter-spacing:.3px}
.nav .active{position:relative}
.nav .active::after{content:"";position:absolute;left:-6px;right:-6px;bottom:-13px;height:3px;background:var(--pink)}

.hero{left:190px;top:184px;width:818px;height:402px;border:6px solid var(--white);box-shadow:0 4px 10px rgba(0,0,0,.35);background:linear-gradient(120deg,#3a2250 0%,#5c2b66 35%,#8a3a4a 65%,#2b3a5a 100%)}
.hero-title{top:170px;font-family:"Montserrat",sans-serif;font-weight:300;font-size:40px;color:var(--white);width:806px;text-align:center;left:0}
.hero-sub{top:232px;width:806px;left:0;text-align:center;font-family:"Montserrat",sans-serif;font-size:14px;color:var(--white)}
.btn{left:333px;top:271px;width:140px;height:32px;border-radius:16px;background:var(--pink);color:var(--white);font-family:"Montserrat",sans-serif;font-size:9px;font-weight:600;line-height:32px;text-align:center;letter-spacing:.3px}
.dots{left:0;width:806px;top:354px;display:flex;justify-content:center;gap:9px}
.dots span{width:7px;height:7px;border-radius:50%;background:var(--white)}
.dots span:first-child{background:#e48ac4}

/* intro */
.h2{font-family:"Montserrat",sans-serif;font-weight:700;color:var(--pink);font-size:28px}
.intro-title{top:690px}
.intro-sub{top:738px;font-size:15px;color:var(--muted)}
.rule{left:300px;top:784px;width:600px;height:1px;background:#e6e6e6}
.intro-copy{left:205px;top:820px;width:790px;text-align:center;font-size:12.5px;line-height:22px;color:var(--muted)}
.contact-row{top:938px;display:flex;justify-content:center;align-items:center;gap:16px;font-family:"Montserrat",sans-serif;font-size:23px;font-weight:300;color:var(--ink)}
.contact-row svg{width:22px;height:22px}

/* services */
.services{top:1054px;left:0;width:1200px;height:458px;background:var(--pink)}
.services .h2{color:var(--white);top:62px}
.service{top:160px;width:270px;text-align:center;color:var(--white)}
.service .icon{width:90px;height:90px;border-radius:50%;background:var(--white);margin:0 auto;display:flex;align-items:center;justify-content:center}
.service .icon svg{width:50px;height:50px}
.service h3{font-family:"Montserrat",sans-serif;font-weight:700;font-size:19px;margin-top:16px}
.service p{font-size:11px;line-height:19px;margin:16px auto 0;width:232px}

/* video */
.video-band{top:1512px;left:0;width:1200px;height:604px;background:#222}
.video-bg{inset:0;background:radial-gradient(ellipse at 30% 40%,#4a4a4a 0%,#2a2a2a 60%,#1c1c1c 100%)}
.video-band .h2{top:56px}
.player{left:270px;top:150px;width:660px;height:335px;border:4px solid var(--white);background:linear-gradient(180deg,#2d2d2d 0%,#6a6a6a 45%,#4a4a4a 75%,#222 100%)}
.play{left:297px;top:110px;width:62px;height:62px}
.controls{left:60px;top:275px;width:532px;height:30px}

/* reviews */
.reviews .h2{top:2163px}
.avatar{left:545px;top:2237px;width:110px;height:110px;border-radius:50%;border:5px solid var(--pink);background:linear-gradient(135deg,#b9a79a,#6f5b4f)}
.reviewer{top:2352px;font-family:"Montserrat",sans-serif;font-size:18px;color:var(--ink)}
.stars{top:2388px;display:flex;justify-content:center;gap:6px}
.stars svg{width:20px;height:20px}
.quote{left:205px;top:2436px;width:790px;text-align:center;font-family:"Montserrat",sans-serif;font-weight:400;font-size:20px;line-height:28px;color:#555}
.arrows{top:2553px;display:flex;justify-content:center;gap:16px}
.arrows svg{width:14px;height:20px}

/* footer */
.footer{top:2615px;left:0;width:1200px;height:233px;background:var(--soft)}
.footer .brand{position:absolute;left:0;width:1200px;top:40px;font-size:25px}
.socials{top:120px;display:flex;justify-content:center;gap:6px}
.socials span{width:19px;height:19px;border-radius:50%;border:1px solid #b5b5b5}
.foot-nav{top:162px;display:flex;justify-content:center;gap:18px;font-family:"Montserrat",sans-serif;font-size:10px;font-weight:500;color:var(--ink)}
.copyright{top:196px;font-family:"Montserrat",sans-serif;font-size:9.5px;color:#555;letter-spacing:.3px}
</style>
</head>
<body>

<header class="abs topbar">
  <div class="abs contact-mini" style="left:203px">
    <svg viewBox="0 0 20 20" fill="none" stroke="#d6309b" stroke-width="1.6"><rect x="2" y="4" width="16" height="12" rx="1"/><path d="M2 5l8 6 8-6"/></svg>
    events@VelmorHall.com
  </div>
  <div class="abs logo-tab"><div class="brand">1927<br>Velmor Hall</div></div>
  <div class="abs contact-mini" style="left:910px">
    <svg viewBox="0 0 20 20" fill="none" stroke="#d6309b" stroke-width="1.6"><circle cx="10" cy="10" r="8.5"/><path d="M7 6l1.5 2-1 1.2c.6 1.3 1.7 2.4 3 3l1.2-1 2 1.5-.9 1.5c-3.2-.3-6.2-3.3-6.5-6.5z" fill="#d6309b" stroke="none"/></svg>
    555.214.0927
  </div>
</header>

<div class="abs grey-band"></div>
<nav class="abs center nav">
  <span class="active">HOME</span><span>WEDDINGS</span><span>EVENTS</span><span>CATERING</span><span>GALLERY</span><span>CONTACT US</span>
</nav>

<section class="abs hero" role="img" aria-label="Photo of the reception hall set for an event, guests seated under warm purple and amber lighting">
  <div class="abs hero-title">1927 Velmor Hall</div>
  <div class="abs hero-sub">Weddings &amp; Events at the 1927 Velmor Hall</div>
  <div class="abs btn">GET STARTED TODAY</div>
  <div class="abs dots"><span></span><span></span><span></span><span></span></div>
</section>

<section class="intro">
  <h2 class="abs center h2 intro-title">Weddings &amp; Events at the 1927 Velmor Hall</h2>
  <p class="abs center intro-sub">Imagine your wedding or event in Larkhaven's premiere, unique and historic venue</p>
  <div class="abs rule"></div>
  <p class="abs intro-copy">When choosing the location for your wedding or event, the 1927 Velmor Hall provides you with an all-inclusive experience, from the moment you arrive, through the creative food, and amazing photo opportunities. The unique open-kitchen provides you, and your guests a front-row seat to our creative, and talented chefs, as they prepare a culinary experience like no other. The full, and spacious bar, serves up wonderful libations and specialty cocktails that enhance your experience.</p>
  <div class="abs center contact-row">
    <svg viewBox="0 0 20 20"><path d="M4 2l3.5 4-2 2.3c1.2 2.6 3.3 4.7 5.9 5.9l2.3-2 4 3.5-2 2.3C9 17.5 2.5 11 2 3.9z" fill="#d6309b"/></svg>
    <span>555.214.0927</span><span>|</span>
    <svg viewBox="0 0 20 20" fill="none" stroke="#d6309b" stroke-width="1.8"><rect x="2" y="4" width="16" height="12" rx="1"/><path d="M2 5l8 6 8-6"/></svg>
    <span>Events@VelmorHall.com</span>
  </div>
</section>

<section class="abs services">
  <h2 class="abs center h2">Our Services</h2>
  <div class="abs service" style="left:190px">
    <div class="icon"><svg viewBox="0 0 50 50" fill="none" stroke="#333" stroke-width="1.8"><circle cx="18" cy="20" r="8"/><circle cx="32" cy="20" r="8"/><path d="M6 44c1-9 6-13 12-13s11 4 12 13M20 44c1-9 6-13 12-13s11 4 12 13"/></svg></div>
    <h3>Weddings</h3>
    <p>Celebrate your day in a bright historic hall with modern touches, warm lighting and a team that handles every small detail for you.</p>
  </div>
  <div class="abs service" style="left:465px">
    <div class="icon"><svg viewBox="0 0 50 50" fill="none" stroke="#333" stroke-width="1.8"><path d="M10 30h30M14 30v14M36 30v14M25 14v16"/><circle cx="25" cy="10" r="4"/><path d="M4 44V24M46 44V24M4 34h6M40 34h6"/></svg></div>
    <h3>Caterings</h3>
    <p>Our chefs cook fresh seasonal menus in the open kitchen, from plated dinners to late night bites and signature cocktails at the bar.</p>
  </div>
  <div class="abs service" style="left:740px">
    <div class="icon"><svg viewBox="0 0 50 50" fill="none" stroke="#333" stroke-width="1.8"><path d="M8 20l17-12 17 12v24H8z"/><path d="M8 20l17 13 17-13"/><path d="M25 27c-4-3-6-5-6-7.5a3 3 0 016-1 3 3 0 016 1c0 2.5-2 4.5-6 7.5z"/></svg></div>
    <h3>Events</h3>
    <p>Host parties, showers, galas and corporate nights in a flexible space with staging, sound and layouts shaped around your guests.</p>
  </div>
</section>

<section class="abs video-band">
  <div class="abs video-bg" role="img" aria-label="Faded black and white photo of the hall during an evening event"></div>
  <h2 class="abs center h2">Featured Video</h2>
  <div class="abs player" role="img" aria-label="Video still of the hall set with round tables, chandeliers and patterned uplighting on the walls">
    <svg class="abs play" viewBox="0 0 62 62"><circle cx="31" cy="31" r="31" fill="#1a1a1a" opacity=".85"/><path d="M25 19l19 12-19 12z" fill="#fff"/></svg>
    <svg class="abs controls" viewBox="0 0 532 30">
      <rect width="532" height="30" rx="3" fill="#111" opacity=".85"/>
      <path d="M14 9l10 6-10 6z" fill="#fff"/>
      <rect x="44" y="12" width="304" height="6" rx="3" fill="#444"/>
      <rect x="44" y="12" width="96" height="6" rx="3" fill="#2a9fd6"/>
      <g fill="#2a9fd6"><rect x="402" y="10" width="2" height="10"/><rect x="406" y="10" width="2" height="10"/><rect x="410" y="10" width="2" height="10"/><rect x="414" y="10" width="2" height="10"/><rect x="418" y="10" width="2" height="10"/><rect x="422" y="10" width="2" height="10"/></g>
      <text x="432" y="20" font-family="Montserrat,sans-serif" font-size="11" font-weight="700" font-style="italic" fill="#2a9fd6">HD</text>
      <path d="M460 10l8 10M468 10l-8 10" stroke="#fff" stroke-width="2"/>
    </svg>
  </div>
</section>

<section class="reviews">
  <h2 class="abs center h2">Our Reviews</h2>
  <div class="abs avatar" role="img" aria-label="Portrait photo of the reviewer"></div>
  <div class="abs center reviewer">Marisol</div>
  <div class="abs center stars">
    <svg viewBox="0 0 20 20"><path d="M10 1l2.6 6 6.4.5-4.9 4.2 1.5 6.3L10 14.6 4.4 18l1.5-6.3L1 7.5 7.4 7z" fill="#f5b21a"/></svg>
    <svg viewBox="0 0 20 20"><path d="M10 1l2.6 6 6.4.5-4.9 4.2 1.5 6.3L10 14.6 4.4 18l1.5-6.3L1 7.5 7.4 7z" fill="#f5b21a"/></svg>
    <svg viewBox="0 0 20 20"><path d="M10 1l2.6 6 6.4.5-4.9 4.2 1.5 6.3L10 14.6 4.4 18l1.5-6.3L1 7.5 7.4 7z" fill="#f5b21a"/></svg>
    <svg viewBox="0 0 20 20"><path d="M10 1l2.6 6 6.4.5-4.9 4.2 1.5 6.3L10 14.6 4.4 18l1.5-6.3L1 7.5 7.4 7z" fill="#f5b21a"/></svg>
    <svg viewBox="0 0 20 20"><path d="M10 1l2.6 6 6.4.5-4.9 4.2 1.5 6.3L10 14.6 4.4 18l1.5-6.3L1 7.5 7.4 7z" fill="#f5b21a"/></svg>
  </div>
  <p class="abs quote">My fiancé and I are extremely excited to start planning our wedding at this amazing venue! Elena and the rest of the staff have been very helpful with the beginning stages of our wedding preparations! :)</p>
  <div class="abs center arrows">
    <svg viewBox="0 0 14 20"><path d="M11 3L4 10l7 7" fill="none" stroke="#d6309b" stroke-width="2.4"/></svg>
    <svg viewBox="0 0 14 20"><path d="M3 3l7 7-7 7" fill="none" stroke="#d6309b" stroke-width="2.4"/></svg>
  </div>
</section>

<footer class="abs footer">
  <div class="brand">1927<br>Velmor Hall</div>
  <div class="abs center socials"><span></span><span></span><span></span><span></span><span></span></div>
  <div class="abs center foot-nav">
    <span>HOME</span><span>|</span><span>WEDDINGS</span><span>|</span><span>EVENTS</span><span>|</span><span>CATERING</span><span>|</span><span>GALLERY</span><span>|</span><span>CONTACT US</span>
  </div>
  <div class="abs center copyright">© 2016 COMPANY NAME &nbsp;| ALL RIGHTS RESERVED</div>
</footer>

</body>
</html>
```